Tech business card design

We need an amazing business card design for our new business 'Pexla' a marketing tech startup based in Sydney, Australia. We provide an online marketplace for businesses to search and buy advertising media, connect with service providers and learn more about marketing. We wish to communicate 'cool tech', reliability and professionalism and design based around our logo.

Target Market(s)

Business Owners

Contact Information for Business Card

Name
Position
Email Address
Website
Phone Number

Font styles to use
Other font styles liked:
• Avenir & Avenir Next

Colors

Designer to choose colors to be used in the design.

```html
<!DOCTYPE html>
<html lang="en">
<head>
<meta charset="utf-8">
<title>Pexla Business Card</title>
<link href="https://fonts.googleapis.com/css2?family=Source+Sans+3:wght@400;700&display=swap" rel="stylesheet">
<style>
  :root {
    --page: #e1dedf;
    --front-bg: #c5c6d9;
    --band-light: #c9c9d5;
    --band-line: #7d7d8a;
    --navy: #11123a;
    --tab: #262848;
    --tab-fold: #1c1e5a;
    --ink: #262a4f;
    --text: #1f1f2e;
    --white: #ffffff;
  }
  * { margin: 0; padding: 0; box-sizing: border-box; }
  html, body { width: 975px; height: 1200px; overflow: hidden; }
  body {
    background: var(--page);
    font-family: "Source Sans 3", "Myriad Pro", sans-serif;
    position: relative;
  }
  .card { position: absolute; left: 57px; width: 861px; overflow: hidden; }
  .card-front { top: 70px; height: 492px; background: var(--front-bg); }
  .card-back {
    top: 627px; left: 58px; width: 860px; height: 490px;
    background: var(--white); border: 1px solid #3a3a3a;
  }
  .name-band {
    position: absolute; left: 3px; top: 167px; width: 858px; height: 142px;
    background: var(--band-light); border: 1px solid var(--band-line);
  }
  .person { position: absolute; left: 72px; top: 192px; color: var(--ink); }
  .person-name { font-weight: 700; font-size: 43px; line-height: 1; letter-spacing: 0.2px; }
  .person-role { font-weight: 400; font-size: 39px; line-height: 1; margin-top: 12px; color: var(--navy); }
  .spine { position: absolute; left: 0; top: 0; }
  .contact {
    position: absolute; left: 526px; color: var(--text);
    font-size: 21px; line-height: 28px;
  }
  .contact-phone { top: 114px; }
  .contact-email { top: 176px; }
  .contact-web { top: 255px; letter-spacing: 2px; }
  .contact-address { top: 326px; }
  .brand-band {
    position: absolute; left: 0; top: 173px; width: 100%; height: 143px;
    background: var(--navy);
    display: flex; align-items: center; justify-content: center;
  }
  .brand-name {
    color: var(--white); font-weight: 700; font-size: 132px;
    line-height: 1; letter-spacing: 1px; margin-top: -6px;
  }
  .back-url {
    position: absolute; left: 0; width: 100%; top: 424px;
    text-align: center; font-size: 29px; letter-spacing: 4px; color: var(--ink);
  }
</style>
</head>
<body>
  <section class="card card-front">
    <div class="name-band"></div>
    <div class="person">
      <h1 class="person-name">JOHN SMITH</h1>
      <p class="person-role">Position</p>
    </div>

    <svg class="spine" width="861" height="492" viewBox="0 0 861 492" aria-hidden="true">
      <rect x="421" y="57" width="46" height="389" fill="var(--navy)"/>
      <g fill="var(--tab-fold)">
        <polygon points="397,151 421,151 421,164"/><polygon points="467,151 491,151 467,164"/>
        <polygon points="397,217 421,217 421,230"/><polygon points="467,217 491,217 467,230"/>
        <polygon points="397,294 421,294 421,307"/><polygon points="467,294 491,294 467,307"/>
        <polygon points="397,371 421,371 421,384"/><polygon points="467,371 491,371 467,384"/>
      </g>
      <g fill="var(--tab)">
        <rect x="398" y="104" width="94" height="48"/>
        <rect x="397" y="170" width="94" height="48"/>
        <rect x="397" y="247" width="94" height="48"/>
        <rect x="397" y="324" width="94" height="48"/>
      </g>
      <g fill="none" stroke="var(--white)" stroke-width="1.6">
        <circle cx="445" cy="127" r="10"/>
        <path d="M440.5 121.5c-1.5 1.5-.5 5 2 7.5s6 3.5 7.5 2l.8-1.3-2.4-1.8-1.4 1c-1.2-.4-3.2-2.4-3.6-3.6l1-1.4-1.8-2.4z" fill="var(--white)" stroke-width="0.6"/>
        <circle cx="444" cy="270" r="9.5"/>
        <ellipse cx="444" cy="270" rx="4" ry="9.5"/>
        <path d="M434.5 270h19M436 265h16M436 275h16"/>
        <circle cx="444" cy="348" r="10.5"/>
        <path d="M444 356c-3.5-4-5.5-7-5.5-9.5a5.5 5.5 0 0 1 11 0c0 2.5-2 5.5-5.5 9.5z"/>
        <circle cx="444" cy="346.5" r="1.8"/>
      </g>
      <g>
        <rect x="434" y="186" width="20" height="14" fill="var(--white)"/>
        <path d="M434 186l10 8 10-8M434 200l7-7M454 200l-7-7" fill="none" stroke="var(--tab)" stroke-width="1.4"/>
      </g>
    </svg>

    <p class="contact contact-phone">012-345-6789</p>
    <p class="contact contact-email">info@pexla.com</p>
    <p class="contact contact-web">www.pexla.com</p>
    <p class="contact contact-address">Street name City Name,<br>Zipcode,012345</p>
  </section>

  <section class="card card-back">
    <div class="brand-band">
      <span class="brand-name">Pexla</span>
    </div>
    <p class="back-url">www.pexla.com</p>
  </section>
</body>
</html>
```